Brovan - Web Design Rebrand for Manufacturing Automation Company

I need a new brand for a customer based in Ireland.
The website currently: https://corvethsystems.example/
Corveth Systems provides a wide range of automation and IT solutions used in manufacturing operations.
Their solutions span a broad spectrum of technology from physical machines and robots to cloud based management solutions for these systems.
They are an Authorised Distributor for Pelmont Controls.
Their partnership with Pelmont Controls will now include working closely to keep track of supply trends and preparing customers for future Data Centre projects.

Essentially their USP:
They have a large team of specialist technical people spanning the breadth of skills to be able to deploy and support automation and IT solutions in manufacturing in the Life Sciences Industry.

Along with Pelmont Controls, they have specialist teams for accelerating Data Center applications.

Competitor websites:
https://www.duravex.example/global/en.html - I really like the layout of their partnerships/collaborations section.
https://global.qtl.example/group/en - Their first moving imagery/tagline and 'discover more' when you enter the site is really eye-catching.
https://www.kv.example/uk/en/ - They layout and structure of the 'The core of what we do section' is really nice.

These are a big companies so anything we could steal would be good 😊

They want:
• Fresh, sharp imagery
• Movement on the main page and perhaps video on some sections? - similar to QTL
• A page to showcase Automation Solutions
• A page to showcase Data Centers
• About us
• Sectors they operate in (includes Life Sciences, Food & Bev, Data Centres)

Industry/Entity Type

Life Science Manufacturing

Number of Pages Required

1 page

Font styles to use
Sans Serif

Colors
0054AA
0677BA
7BADD7
CADEEF
E8F1F8

Requirements
Must have
• Moving Imagery

```html
<!DOCTYPE html>
<html lang="en">
<head>
<meta charset="utf-8">
<title>Corveth Systems</title>
<link href="https://fonts.googleapis.com/css2?family=Russo+One&family=Roboto:wght@400;500;700&display=swap" rel="stylesheet">
<style>
:root{
  --blue:#1c9ad6;
  --blue-deep:#0677ba;
  --navy:#0b1a3a;
  --grey-head:#4a4d52;
  --text:#6b6f75;
  --ink:#1d1f23;
  --white:#ffffff;
  --band:#1a9bd7;
  --footer:#15171b;
  --pale:#e8f1f8;
  --map:#e6e8eb;
}
*{box-sizing:border-box;margin:0;padding:0}
html,body{width:1200px;height:4234px;overflow:hidden}
body{font-family:"Roboto",Arial,sans-serif;color:var(--text);background:var(--white);position:relative}
.display{font-family:"Russo One","Arial Black",sans-serif;text-transform:uppercase;letter-spacing:1px}
.display .accent{color:var(--blue)}
.display .rest{color:var(--grey-head)}
.abs{position:absolute}

/* header */
.site-header{top:0;left:0;width:1200px;height:107px;background:var(--white);border-top:4px solid var(--blue);box-shadow:0 1px 6px rgba(0,0,0,.08)}
.brand{left:112px;top:34px;display:flex;align-items:center;gap:12px;font-weight:500;font-size:24px;color:var(--blue);letter-spacing:1px}
.brand-mark{width:34px;height:34px;background:var(--blue)}
.nav{top:44px;left:590px;display:flex;gap:56px;font-size:13px;color:#444}
.nav-social{left:1070px;top:43px;width:18px;height:18px;background:var(--blue);border-radius:2px}

/* hero */
.hero{top:107px;left:0;width:1200px;height:562px;background:radial-gradient(ellipse at 60% 45%,#1d3550 0%,#101822 55%,#07090d 100%)}
.hero-bar{left:548px;top:96px;width:104px;height:6px;background:var(--blue);border-radius:3px}
.hero-title{left:0;top:140px;width:1200px;text-align:center;font-weight:700;font-size:74px;color:var(--white);letter-spacing:2px}
.hero-lead{left:0;top:244px;width:1200px;text-align:center;font-size:17px;line-height:36px;color:#eef2f6}
.btn{display:inline-block;font-size:14px;font-weight:700;padding:10px 28px;transform:skewX(-14deg)}
.btn span{display:inline-block;transform:skewX(14deg)}
.btn-blue{background:var(--blue);color:var(--white)}
.btn-white{background:var(--white);color:var(--blue)}
.hero-actions{left:0;top:344px;width:1200px;display:flex;justify-content:center;gap:18px}
.discover{left:0;top:492px;width:1200px;text-align:center;color:#fff;font-size:13px}
.pause{left:1140px;top:503px;width:24px;height:24px;border-radius:50%;background:#fff}

/* about */
.about-title{left:112px;top:828px;font-size:44px}
.about-text{left:112px;top:898px;width:440px;font-size:13px;line-height:31px;color:var(--text)}
.about-text p+p{margin-top:31px}
.about-btn{left:118px;top:1237px}
.dots{left:895px;top:1200px;width:300px;height:200px;background-image:radial-gradient(#d2d6da 1.3px,transparent 1.5px);background-size:9px 9px}
.about-media{left:600px;top:791px;width:487px;height:527px;background:linear-gradient(135deg,#071437 0%,#0c3a7a 50%,#0a1a40 100%);box-shadow:0 10px 30px rgba(0,0,0,.25)}

/* sectors */
.section-title{left:0;width:1200px;text-align:center;font-size:42px}
.sectors-lead{left:180px;top:1500px;width:840px;text-align:center;font-size:15.5px;line-height:34px;color:#555}
.tile{top:1615px;width:399px;height:451px}
.tile-label{position:absolute;left:50px;bottom:38px;color:#fff;font-weight:700;font-size:18px}
.tile-life{left:0;background:linear-gradient(150deg,#0a3f7c,#1a6fb8 55%,#083062)}
.tile-food{left:401px;background:linear-gradient(160deg,#2a1a0e,#7a4a1e 55%,#a38a2a)}
.tile-data{left:802px;background:linear-gradient(160deg,#0c1c35,#2c4d72 55%,#122a48)}

/* partners */
.partner{background:#fff;box-shadow:0 6px 26px rgba(0,0,0,.08);text-align:center}
.partner-card{top:2288px;width:242px;height:317px;padding:0 22px}
.partner-name{margin-top:60px;font-size:34px;font-weight:700;color:#2c2f33;letter-spacing:-1px}
.partner-name.blue{color:#1d4fa3}
.partner-copy{margin-top:24px;font-size:11.5px;line-height:25px;color:#777}
.partner-arrow{margin:18px auto 0;width:14px;height:14px;border-radius:50%;background:var(--blue);position:relative}
.partner-arrow::after{content:"";position:absolute;left:4px;top:4px;width:4px;height:4px;border-top:2px solid #fff;border-right:2px solid #fff;transform:rotate(45deg)}
.badge-shape{margin:64px auto 0;width:180px;height:52px;display:flex;align-items:center;gap:10px}
.badge-shape i{display:block;width:52px;height:52px;border-radius:50%;background:#d7282f}
.badge-shape b{display:block;flex:1;height:30px;background:#e4e6e9}
.partner-featured{left:342px;top:2265px;width:271px;height:363px}
.featured-media{width:271px;height:268px;background:linear-gradient(160deg,#0f2a45,#3a5f82 55%,#1a2b3c)}
.featured-name{margin-top:26px;font-size:28px;color:#2c2f33;letter-spacing:1px}

/* contact band */
.contact-band{top:2730px;left:0;width:1200px;height:257px;background:var(--band)}
.contact-item{top:60px;width:300px;text-align:center;color:#fff;font-size:13.5px;line-height:25px}
.contact-icon{width:62px;height:62px;border-radius:50%;background:#6c7379;margin:0 auto 22px;display:flex;align-items:center;justify-content:center}

/* customers */
.map-area{left:107px;top:3181px;width:986px;height:592px;border-radius:60px 60px 120px 120px;background:linear-gradient(180deg,#e9ebee 0%,var(--map) 50%,#eceef0 100%)}
.map-pin{width:16px;height:22px}
.map-badge{left:769px;top:3571px;width:66px;height:66px;border-radius:50%;background:#fff;border:3px solid #2a2c30;box-shadow:0 4px 12px rgba(0,0,0,.25)}

/* footer */
.site-footer{top:3865px;left:0;width:1200px;height:369px;background:radial-gradient(ellipse at 20% 30%,#23262b,var(--footer) 70%)}
.footer-brand{left:112px;top:135px;display:flex;align-items:center;gap:14px}
.footer-brand-mark{width:46px;height:46px;background:var(--blue)}
.footer-brand-name{font-size:30px;line-height:32px;font-weight:500;color:#9ea3a8;letter-spacing:2px}
.footer-brand-name span{color:var(--blue)}
.footer-col{top:80px}
.footer-col h3{font-size:21px;color:#fff;font-weight:400;margin-bottom:18px}
.footer-col li{list-style:none;font-size:12px;color:#e3e5e8;line-height:32px}
.footer-rule{left:112px;top:296px;width:976px;height:1px;background:#3a3d42}
.copyright{left:0;top:327px;width:1200px;text-align:center;font-size:10px;color:#d0d3d6}
</style>
</head>
<body>

<header class="site-header abs">
  <div class="brand abs"><span class="brand-mark"></span>CORVETH SYSTEMS</div>
  <nav class="nav abs"><span>Robotics &amp; Automation Solutions</span><span>About Us</span><span>Contact Us</span></nav>
  <span class="nav-social abs"></span>
</header>

<section class="hero abs" role="img" aria-label="Hand touching a glowing digital network of automation icons">
  <div class="hero-bar abs"></div>
  <h1 class="hero-title abs">CORVETH SYSTEMS</h1>
  <p class="hero-lead abs">We provide a wide range of robotics and automation solutions that are used in factories,<br>logistics and healthcare environments.</p>
  <div class="hero-actions abs">
    <a class="btn btn-blue"><span>Get Started</span></a>
    <a class="btn btn-white"><span>Contact Us</span></a>
  </div>
  <div class="discover abs">Discover More<br>
    <svg width="12" height="10" viewBox="0 0 12 10"><path d="M2 3l4 4 4-4" stroke="#fff" stroke-width="2" fill="none"/></svg>
  </div>
  <div class="pause abs">
    <svg width="24" height="24" viewBox="0 0 24 24"><rect x="8.5" y="8" width="2.5" height="8" fill="#111"/><rect x="13" y="8" width="2.5" height="8" fill="#111"/></svg>
  </div>
</section>

<section class="about">
  <h2 class="about-title display abs"><span class="accent">About</span> <span class="accent">Us</span></h2>
  <div class="about-text abs">
    <p>Corveth Systems provides a wide range of automation and IT solutions used in manufacturing operations. Our solutions span a broad spectrum of technology from physical machines and robots to cloud based management solutions for these systems.</p>
    <p>Along with Pelmont Controls, we work closely to keep track of supply trends and invest wisely to prepare for customers' future DC projects. We have a large team of specialist technical people spanning the breadth of skills to be able to deploy and support these technologies. Authorised Distributor for Pelmont Controls</p>
  </div>
  <a class="btn btn-blue about-btn abs"><span>Read More</span></a>
  <div class="dots abs"></div>
  <div class="about-media abs" role="img" aria-label="Hands holding a tablet projecting a holographic control interface"></div>
</section>

<section class="sectors">
  <h2 class="section-title display abs" style="top:1428px"><span class="accent">Our</span> <span class="rest">Sectors</span></h2>
  <p class="sectors-lead abs">Our solutions span a broad spectrum of technology from physical machines and robots through to cloud-based management and data gathering solutions for those systems Continue Reading.</p>
  <div class="tile tile-life abs" role="img" aria-label="Blue molecular structure"><span class="tile-label">LIFE SCIENCES</span></div>
  <div class="tile tile-food abs" role="img" aria-label="Burgers and fries served on a wooden board"><span class="tile-label">FOOD &amp; BEV</span></div>
  <div class="tile tile-data abs" role="img" aria-label="Engineers walking through a server room"><span class="tile-label">DATA CENTRES</span></div>
</section>

<section class="partners">
  <h2 class="section-title display abs" style="top:2163px"><span class="accent">Corveth Technology</span> <span class="rest">Partners</span></h2>
  <div class="partner partner-card abs" style="left:99px">
    <div class="partner-name">Trelvik</div>
    <p class="partner-copy">In 1990, Owen Garrick created a module to connect a Pelmont Controls® processor to a Fieldnet® SCADA host</p>
    <div class="partner-arrow"></div>
  </div>
  <div class="partner partner-featured abs">
    <div class="featured-media" role="img" aria-label="Hands typing on a laptop with security icons"></div>
    <div class="featured-name">vantrel</div>
  </div>
  <div class="partner partner-card abs" style="left:614px">
    <div class="partner-name blue">NORSADE</div>
    <p class="partner-copy">Taking the first step on any automation journey can be a daunting task. Download our guide as we walk</p>
    <div class="partner-arrow"></div>
  </div>
  <div class="partner partner-card abs" style="left:858px">
    <div class="badge-shape"><i></i><b></b></div>
    <p class="partner-copy" style="margin-top:20px">Explore the latest trends and best practices to help you stay competitive, increase agility, &amp;unlock long-term opportunities.</p>
    <div class="partner-arrow"></div>
  </div>
</section>

<section class="contact-band abs">
  <div class="contact-item abs" style="left:122px">
    <div class="contact-icon"><svg width="22" height="26" viewBox="0 0 22 26"><path d="M11 1a9 9 0 0 0-9 9c0 7 9 15 9 15s9-8 9-15a9 9 0 0 0-9-9z" fill="#fff"/><circle cx="11" cy="10" r="3.5" fill="#6c7379"/></svg></div>
    Aldery House, Kestrel Business Park,<br>Lusk, Co. Dublin
  </div>
  <div class="contact-item abs" style="left:450px">
    <div class="contact-icon"><svg width="24" height="18" viewBox="0 0 24 18"><rect x="1" y="1" width="22" height="16" rx="2" fill="#fff"/><path d="M2 2l10 8 10-8" stroke="#6c7379" stroke-width="2" fill="none"/></svg></div>
    Email Address:<br>sales@corvethsystems.example
  </div>
  <div class="contact-item abs" style="left:777px">
    <div class="contact-icon"><svg width="22" height="22" viewBox="0 0 24 24"><path d="M6.6 10.8a15 15 0 0 0 6.6 6.6l2.2-2.2a1 1 0 0 1 1-.25 11.4 11.4 0 0 0 3.6.57 1 1 0 0 1 1 1V20a1 1 0 0 1-1 1A17 17 0 0 1 3 4a1 1 0 0 1 1-1h3.5a1 1 0 0 1 1 1c0 1.25.2 2.45.57 3.57a1 1 0 0 1-.25 1z" fill="#fff"/></svg></div>
    Contact Number:<br>+353 21 555 0147 ( CORK )
  </div>
</section>

<section class="customers">
  <h2 class="section-title display abs" style="top:3066px"><span class="accent">Our</span> <span class="rest">Customers</span></h2>
  <div class="map-area abs" role="img" aria-label="Dotted grey world map showing customer locations"></div>
  <svg class="map-pin abs" style="left:827px;top:3282px" viewBox="0 0 16 22"><path d="M8 0a8 8 0 0 0-8 8c0 6 8 14 8 14s8-8 8-14a8 8 0 0 0-8-8z" fill="#1c9ad6"/><circle cx="8" cy="8" r="3" fill="#fff"/></svg>
  <svg class="map-pin abs" style="left:1026px;top:3332px" viewBox="0 0 16 22"><path d="M8 0a8 8 0 0 0-8 8c0 6 8 14 8 14s8-8 8-14a8 8 0 0 0-8-8z" fill="#1c9ad6"/><circle cx="8" cy="8" r="3" fill="#fff"/></svg>
  <svg class="map-pin abs" style="left:668px;top:3389px" viewBox="0 0 16 22"><path d="M8 0a8 8 0 0 0-8 8c0 6 8 14 8 14s8-8 8-14a8 8 0 0 0-8-8z" fill="#1c9ad6"/><circle cx="8" cy="8" r="3" fill="#fff"/></svg>
  <svg class="map-pin abs" style="left:918px;top:3381px" viewBox="0 0 16 22"><path d="M8 0a8 8 0 0 0-8 8c0 6 8 14 8 14s8-8 8-14a8 8 0 0 0-8-8z" fill="#1c9ad6"/><circle cx="8" cy="8" r="3" fill="#fff"/></svg>
  <svg class="map-pin abs" style="left:812px;top:3417px" viewBox="0 0 16 22"><path d="M8 0a8 8 0 0 0-8 8c0 6 8 14 8 14s8-8 8-14a8 8 0 0 0-8-8z" fill="#1c9ad6"/><circle cx="8" cy="8" r="3" fill="#fff"/></svg>
  <svg class="map-pin abs" style="left:875px;top:3460px" viewBox="0 0 16 22"><path d="M8 0a8 8 0 0 0-8 8c0 6 8 14 8 14s8-8 8-14a8 8 0 0 0-8-8z" fill="#1c9ad6"/><circle cx="8" cy="8" r="3" fill="#fff"/></svg>
  <svg class="map-pin abs" style="left:623px;top:3501px" viewBox="0 0 16 22"><path d="M8 0a8 8 0 0 0-8 8c0 6 8 14 8 14s8-8 8-14a8 8 0 0 0-8-8z" fill="#1c9ad6"/><circle cx="8" cy="8" r="3" fill="#fff"/></svg>
  <svg class="map-pin abs" style="left:773px;top:3488px" viewBox="0 0 16 22"><path d="M8 0a8 8 0 0 0-8 8c0 6 8 14 8 14s8-8 8-14a8 8 0 0 0-8-8z" fill="#1c9ad6"/><circle cx="8" cy="8" r="3" fill="#fff"/></svg>
  <svg class="map-pin abs" style="left:793px;top:3516px" viewBox="0 0 16 22"><path d="M8 0a8 8 0 0 0-8 8c0 6 8 14 8 14s8-8 8-14a8 8 0 0 0-8-8z" fill="#1c9ad6"/><circle cx="8" cy="8" r="3" fill="#fff"/></svg>
  <svg class="map-pin abs" style="left:523px;top:3526px" viewBox="0 0 16 22"><path d="M8 0a8 8 0 0 0-8 8c0 6 8 14 8 14s8-8 8-14a8 8 0 0 0-8-8z" fill="#1c9ad6"/><circle cx="8" cy="8" r="3" fill="#fff"/></svg>
  <svg class="map-pin abs" style="left:674px;top:3575px" viewBox="0 0 16 22"><path d="M8 0a8 8 0 0 0-8 8c0 6 8 14 8 14s8-8 8-14a8 8 0 0 0-8-8z" fill="#1c9ad6"/><circle cx="8" cy="8" r="3" fill="#fff"/></svg>
  <svg class="map-pin abs" style="left:403px;top:3578px" viewBox="0 0 16 22"><path d="M8 0a8 8 0 0 0-8 8c0 6 8 14 8 14s8-8 8-14a8 8 0 0 0-8-8z" fill="#1c9ad6"/><circle cx="8" cy="8" r="3" fill="#fff"/></svg>
  <svg class="map-pin abs" style="left:926px;top:3628px" viewBox="0 0 16 22"><path d="M8 0a8 8 0 0 0-8 8c0 6 8 14 8 14s8-8 8-14a8 8 0 0 0-8-8z" fill="#1c9ad6"/><circle cx="8" cy="8" r="3" fill="#fff"/></svg>
  <div class="map-badge abs"></div>
</section>

<footer class="site-footer abs">
  <div class="footer-brand abs">
    <div class="footer-brand-name"><span>CORVETH</span><br>SYSTEMS</div>
    <span class="footer-brand-mark"></span>
  </div>
  <div class="footer-col abs" style="left:487px">
    <h3 class="display"><span class="accent">Quick</span> Links</h3>
    <ul><li>Automation Solutions</li><li>Data Centers</li><li>About Us</li><li>Contact Us</li></ul>
  </div>
  <div class="footer-col abs" style="left:718px">
    <h3 class="display"><span class="accent">Our</span> Sectors</h3>
    <ul><li>Life Sciences</li><li>Food &amp; Beverages</li><li>Data Centres</li></ul>
  </div>
  <div class="footer-col abs" style="left:961px">
    <h3 class="display"><span class="accent">Find</span> Us On</h3>
    <ul><li>Dublin</li><li>Cork</li><li>Northern Ireland</li></ul>
  </div>
  <div class="footer-rule abs"></div>
  <p class="copyright abs">(C) Copyright 2024 | All Rights Reserved</p>
</footer>

</body>
</html>
```